Business Card for my New Brokerage

Looking to get a business card design for my new Real Estate Brokerage.
I want it with Picture, Phone Number, Email, Website, Office Address
Name and Designation. Please add logo too.

Target Market(s)

Real Estate Investors or Home Buyers

Industry/Entity Type

Real Estate

Contact Information for Business Card

Name, Email, Phone Number, website, email, office address

Colors
EB3D1F
EC4F4E
F09395
F8D3D4
FCEDEE

Requirements
Must have
• Minimalistic, Clean, Modern, Photo
Nice to have
• White and Red Colors

```html
<!DOCTYPE html>
<html lang="en">
<head>
<meta charset="UTF-8">
<title>Beacon Realty Inc – Business Card</title>
<link href="https://fonts.googleapis.com/css2?family=Poppins:wght@400;600;700&display=swap" rel="stylesheet">
<style>
  :root {
    --brand-red: #e01f26;
    --paper: #ffffff;
    --ink: #1c1c1c;
    --gold: #d9b65a;
    --backdrop: #ececec;
    --photo-tone-a: #dfe3ea;
    --photo-tone-b: #9aa6b8;
  }
  * { margin: 0; padding: 0; box-sizing: border-box; }
  html, body {
    width: 1200px; height: 948px; overflow: hidden;
    background: var(--backdrop);
    font-family: "Poppins", sans-serif;
  }
  .canvas {
    position: relative; width: 1200px; height: 948px;
    display: flex; flex-direction: column; align-items: center; justify-content: center; gap: 26px;
  }
  .card {
    position: relative; width: 720px; height: 411px;
    box-shadow: 0 10px 28px rgba(0,0,0,0.18);
  }

  /* Front */
  .card-front {
    background: var(--brand-red);
    display: flex; align-items: center; justify-content: center;
  }
  .front-name {
    color: var(--paper);
    font-weight: 600; font-size: 62px; line-height: 1; letter-spacing: 0;
    white-space: nowrap;
  }

  /* Back */
  .card-back { background: var(--brand-red); padding: 16px; }
  .back-inner { position: relative; width: 100%; height: 100%; background: var(--paper); }
  .portrait-frame {
    position: absolute; left: 150px; top: 62px;
    width: 256px; height: 256px; border-radius: 50%;
    border: 4px solid var(--gold);
    padding: 6px;
  }
  .portrait {
    width: 100%; height: 100%; border-radius: 50%;
    background: radial-gradient(circle at 50% 75%, var(--photo-tone-b), var(--photo-tone-a) 70%);
  }
  .divider {
    position: absolute; left: 436px; top: 70px;
    width: 1.5px; height: 250px; background: var(--brand-red);
  }
  .details { position: absolute; left: 462px; top: 62px; color: var(--ink); }
  .back-name {
    color: var(--brand-red);
    font-weight: 600; font-size: 24px; line-height: 1.1; white-space: nowrap;
  }
  .person-name {
    margin-top: 22px; color: var(--brand-red);
    font-weight: 700; font-size: 19px; line-height: 1.1;
  }
  .person-title { font-size: 12.5px; margin-top: 2px; }
  .address { font-size: 12.5px; line-height: 1.45; margin-top: 12px; }
  .contact-list { list-style: none; margin-top: 12px; font-size: 12.5px; line-height: 1.75; }
  .contact-list li { display: flex; align-items: center; gap: 8px; }
  .contact-list svg { width: 12px; height: 12px; flex: none; }
</style>
</head>
<body>
<main class="canvas">

  <section class="card card-front" aria-label="Card front">
    <div class="front-name">Beacon Realty Inc</div>
  </section>

  <section class="card card-back" aria-label="Card back">
    <div class="back-inner">
      <div class="portrait-frame">
        <div class="portrait" role="img" aria-label="Portrait photo of the broker in a navy blazer and light shirt"></div>
      </div>
      <div class="divider"></div>
      <div class="details">
        <div class="back-name">Beacon Realty Inc</div>
        <div class="person-name">DANIEL MARSH</div>
        <div class="person-title">Owner/CEO</div>
        <div class="address">1480 W Harlow Avenue<br>Fenwick County 6420</div>
        <ul class="contact-list">
          <li>
            <svg viewBox="0 0 24 24" aria-hidden="true"><path fill="#e01f26" d="M6.6 10.8a15.1 15.1 0 0 0 6.6 6.6l2.2-2.2a1 1 0 0 1 1-.25 11.4 11.4 0 0 0 3.6.57 1 1 0 0 1 1 1V20a1 1 0 0 1-1 1A17 17 0 0 1 3 4a1 1 0 0 1 1-1h3.5a1 1 0 0 1 1 1c0 1.250.2 2.450.57 3.57a1 1 0 0 1-.25 1z"/></svg>
            123-555-0187
          </li>
          <li>
            <svg viewBox="0 0 24 24" aria-hidden="true"><rect x="2" y="5" width="20" height="14" fill="#e01f26"/><path d="M2 5l10 8 10-8" fill="none" stroke="#fff" stroke-width="2"/></svg>
            info@beaconrealtyinc.com
          </li>
          <li>
            <svg viewBox="0 0 24 24" aria-hidden="true"><circle cx="12" cy="12" r="10" fill="#e01f26"/><path d="M2 12h20M12 2c3 3 3 17 0 20M12 2c-3 3-3 17 0 20" fill="none" stroke="#fff" stroke-width="1.5"/></svg>
            www.beaconrealtyinc.com
          </li>
        </ul>
      </div>
    </div>
  </section>

</main>
</body>
</html>
```